Social Media App Needs PPT Template

We need a PowerPoint template for a new social media company based in the DC area called "Bold Ledger." We provide an interactive digital platform for executives to share actionable advice. We would like to see designs that use our orange logo color as an accent, but are mainly grey, white, and black. The final design should communicate clean, chic, modern, and professional.

Target Market(s)

Executives

Industry/Entity Type

Information Technology

Font styles to use
Sans Serif

Colors
f78f20
fbe7d2
ffffff
000000
e8e8e8
757575

Requirements
Must have
• My project must have title page and many options for the body of the ppt (graphs, tables, etc). It also needs to be easy to modify. I must have someone who is experienced in creating powerpoint templates.
Nice to have
• It would be nice to have a very modern and clean design that includes the logo on every page, but still leaves a lot of room for the content of the slide
Should not have
• My design project should not look to busy.

```html
<!DOCTYPE html>
<html lang="en">
<head>
<meta charset="utf-8">
<title>About Our Company – Bold Ledger</title>
<link href="https://fonts.googleapis.com/css2?family=Bebas+Neue&family=Lato:wght@300;400&display=swap" rel="stylesheet">
<style>
  :root {
    --stage: #555555;
    --white: #ffffff;
    --navy: #232d3b;
    --orange: #f78f20;
    --ink: #3f3f3f;
    --muted: #757575;
    --rule: #555555;
  }
  * { margin: 0; padding: 0; box-sizing: border-box; }
  html, body { width: 1200px; height: 960px; overflow: hidden; }
  body {
    position: relative;
    background: var(--stage);
    font-family: 'Lato', sans-serif;
  }
  .page-label {
    position: absolute;
    top: 74px; left: 0; width: 1200px;
    text-align: center;
    color: var(--white);
    font-weight: 300;
    font-size: 28px;
  }
  .slide {
    position: absolute;
    left: 123px; top: 159px;
    width: 987px; height: 741px;
    background: var(--white);
  }
  .accent-stripe {
    position: absolute;
    left: 0; top: 15px; width: 100%; height: 11px;
    background: var(--orange);
  }
  .title-band {
    position: absolute;
    left: 0; top: 29px; width: 100%; height: 95px;
    background: var(--navy);
  }
  .slide-title {
    position: absolute;
    left: 43px; top: 22px;
    font-family: 'Bebas Neue', sans-serif;
    font-weight: 400;
    font-size: 60px;
    line-height: 1;
    color: var(--white);
    letter-spacing: 0.2px;
  }
  .brand {
    position: absolute;
    right: 38px; top: 31px;
    display: flex; align-items: center; gap: 10px;
  }
  .brand-dot {
    width: 26px; height: 26px; border-radius: 50%;
    background: var(--orange);
  }
  .brand-name {
    font-family: 'Lato', sans-serif;
    font-weight: 400;
    font-size: 28px;
    color: var(--white);
    letter-spacing: 1px;
  }
  .feature-visual {
    position: absolute;
    left: 83px; top: 197px;
    width: 350px; height: 260px;
    border-radius: 6px;
    background: radial-gradient(ellipse at 50% 45%, #4da3e0 0%, #6fc0ea 38%, #e9f3fa 75%, #ffffff 100%);
  }
  .intro-text {
    position: absolute;
    left: 60px; top: 481px;
    width: 411px;
    font-size: 19px;
    line-height: 23.3px;
    color: var(--ink);
    text-align: justify;
  }
  .key-points {
    position: absolute;
    left: 530px; top: 235px;
    width: 420px;
    list-style: none;
  }
  .key-points li {
    position: relative;
    padding-left: 25px;
    font-size: 20px;
    line-height: 30px;
    color: var(--ink);
    margin-bottom: 29px;
  }
  .key-points li::before {
    content: "";
    position: absolute;
    left: 0; top: 10px;
    width: 10px; height: 10px;
    background: var(--orange);
  }
  .footer-rule {
    position: absolute;
    left: 663px; top: 684px;
    width: 287px; height: 1px;
    background: var(--rule);
  }
  .footer-meta {
    position: absolute;
    right: 35px; top: 702px;
    font-size: 13.5px;
    color: var(--muted);
  }
</style>
</head>
<body>
  <div class="page-label">Page 4</div>

  <section class="slide">
    <div class="accent-stripe"></div>
    <header class="title-band">
      <h1 class="slide-title">About Our Company</h1>
      <div class="brand">
        <span class="brand-dot"></span>
        <span class="brand-name">Bold Ledger</span>
      </div>
    </header>

    <div class="feature-visual" role="img" aria-label="Illustration of a laptop surrounded by colorful floating app icons"></div>

    <p class="intro-text">Duis autem vel eum iriure dolor in hendrerit in vulputate velit esse molestie consequat, vel illum dolore eu feugiat nulla facilisis at vero eros et accumsan et iusto odio dignissim qui blandit praesent luptatum zzril delenit augue duis dolore te feugait nulla facilisi.</p>

    <ul class="key-points">
      <li>Souvlaki ignitus carborundum e pluribus unum.</li>
      <li>Defacto lingo est igpay atinlay. Marquee selectus non provisio.</li>
      <li>Quote meon an estimate et non interruptus stadium.</li>
      <li>Sic tempus fugit esperanto hiccup estrogen.</li>
      <li>Epsum factorial non deposit quid pro quo hic escorol.</li>
    </ul>

    <div class="footer-rule"></div>
    <div class="footer-meta">www.boldledger.com &nbsp;|&nbsp; Page 2</div>
  </section>
</body>
</html>
```